Copperleaf Roofing Business Card

This is my current business card. But I’d like to make some changes. Somewhere on the card I’d like to list some of the services we offer. Maybe on the back? But I’d still like to keep the red. White and black modern look.

-residential & commercial roofing
-Roof Repairs & Maintenance
-Storm Damage & Insurance Claims specialist
-Christmas Lights and permanent Christmas lights
Fencing. Windows. Gutters. Siding. Sheetrock, painting.

```html
<!DOCTYPE html>
<html lang="en">
<head>
<meta charset="utf-8">
<title>Copperleaf Roofing Co. — Business Card</title>
<link rel="stylesheet" href="https://fonts.googleapis.com/css2?family=Orbitron:wght@800&family=Montserrat:wght@400;500&display=swap">
<style>
  :root {
    --stage: #3a3a3a;
    --card-dark: #121212;
    --card-light: #ffffff;
    --red: #e0141e;
    --ink: #111111;
    --muted: #333333;
    --faint: rgba(224, 20, 30, 0.06);
  }
  * { box-sizing: border-box; margin: 0; padding: 0; }
  html, body { width: 1200px; height: 875px; overflow: hidden; }
  body {
    background: var(--stage);
    font-family: "Montserrat", sans-serif;
    position: relative;
  }
  .card {
    position: absolute;
    top: 283px;
    width: 540px;
    height: 309px;
    border-radius: 18px;
    overflow: hidden;
    box-shadow: 0 18px 40px rgba(0,0,0,.45);
  }
  .card--back { left: 40px; background: var(--card-dark); }
  .card--front { left: 620px; background: var(--card-light); }

  .brand {
    display: flex;
    align-items: center;
    gap: 14px;
  }
  .brand__dot {
    flex: none;
    border-radius: 50%;
    background: var(--red);
  }
  .brand__name {
    font-family: "Orbitron", sans-serif;
    font-weight: 800;
    color: var(--red);
    text-transform: uppercase;
    line-height: 1.05;
    letter-spacing: .02em;
  }

  .card--back .brand {
    position: absolute;
    inset: 0;
    justify-content: center;
  }
  .card--back .brand__dot { width: 70px; height: 70px; }
  .card--back .brand__name { font-size: 30px; }

  .card--front .brand { position: absolute; left: 30px; top: 34px; }
  .card--front .brand__dot { width: 46px; height: 46px; }
  .card--front .brand__name { font-size: 19px; }

  .faint-disc {
    position: absolute;
    right: -40px;
    top: 20px;
    width: 230px;
    height: 230px;
    border-radius: 50%;
    background: var(--faint);
  }

  .person { position: absolute; left: 30px; top: 130px; }
  .person__name {
    font-family: "Orbitron", sans-serif;
    font-weight: 800;
    font-size: 22px;
    color: var(--ink);
    letter-spacing: .03em;
  }
  .person__name span { color: var(--red); }
  .person__role { font-size: 12px; color: var(--muted); margin-top: 2px; }

  .contacts { position: absolute; left: 30px; top: 196px; list-style: none; }
  .contacts li {
    display: flex;
    align-items: center;
    gap: 8px;
    font-size: 12px;
    color: var(--ink);
    margin-bottom: 7px;
  }
  .contacts svg { width: 14px; height: 14px; flex: none; }

  .services {
    position: absolute;
    right: 26px;
    top: 62px;
    list-style: none;
    text-align: right;
  }
  .services li {
    font-size: 11.5px;
    color: var(--ink);
    line-height: 1.55;
  }
  .services .bullet::after {
    content: "";
    display: inline-block;
    width: 5px;
    height: 5px;
    margin-left: 6px;
    border-radius: 50%;
    background: var(--red);
    vertical-align: middle;
  }
</style>
</head>
<body>
  <section class="card card--back" aria-label="Card back">
    <div class="brand">
      <span class="brand__dot"></span>
      <span class="brand__name">Copperleaf<br>Roofing Co.</span>
    </div>
  </section>

  <section class="card card--front" aria-label="Card front">
    <div class="faint-disc"></div>

    <div class="brand">
      <span class="brand__dot"></span>
      <span class="brand__name">Copperleaf<br>Roofing Co.</span>
    </div>

    <div class="person">
      <p class="person__name">DALE <span>MERCER</span></p>
      <p class="person__role">Owner</p>
    </div>

    <ul class="contacts">
      <li>
        <svg viewBox="0 0 16 16" aria-hidden="true"><circle cx="8" cy="8" r="8" fill="var(--red)"/><path d="M5.2 4.2l1.4-.3.8 1.9-.9.7a5 5 0 0 0 2.9 2.9l.7-.9 1.9.8-.3 1.4c-3.4.2-6.7-3.1-6.5-6.5z" fill="#fff"/></svg>
        555-014-2290
      </li>
      <li>
        <svg viewBox="0 0 16 16" aria-hidden="true"><circle cx="8" cy="8" r="8" fill="var(--red)"/><rect x="4" y="5.2" width="8" height="5.6" rx=".6" fill="#fff"/><path d="M4.3 5.6L8 8.5l3.7-2.9" fill="none" stroke="var(--red)" stroke-width=".8"/></svg>
        dale@copperleafroofing.com
      </li>
      <li>
        <svg viewBox="0 0 16 16" aria-hidden="true"><circle cx="8" cy="8" r="8" fill="var(--red)"/><circle cx="8" cy="8" r="4" fill="none" stroke="#fff" stroke-width="1"/><ellipse cx="8" cy="8" rx="1.7" ry="4" fill="none" stroke="#fff" stroke-width=".8"/><path d="M4 8h8" stroke="#fff" stroke-width=".8"/></svg>
        www.copperleafroofing.com
      </li>
    </ul>

    <ul class="services">
      <li class="bullet">residential &amp; commercial roofing</li>
      <li class="bullet">Roof Repairs &amp; Maintenance</li>
      <li>Storm Damage &amp;</li>
      <li class="bullet">Insurance Claims specialist</li>
      <li class="bullet">Fencing. Windows. Gutters.</li>
      <li>Siding. Sheetrock, painting</li>
    </ul>
  </section>
</body>
</html>
```